BRELWINCare.co.uk - Mental Health Clinic for Child and Adolescents

Updated 29/01/2018***
I am not sure you guys are getting the idea regards to the opening page / homescreen layout. Can you look at the new images I have uploaded (page 5, 6 and 7) These are some of the layouts I like but to incorporate my chosen images, with the BRELWIN commissioner, buttons and a sliding header bar.
I have written a strong brief, I am looking for a website, preferably wordpress as i know they are easy to maintain. I am looking for a one page site, with the top / opening page being full screen image with drop down categories. I have made a rough design, see full brief in word doc attached, there is some freedom to play around with the design aspect but it will need to relay all the content provided. I like a minimal feel. I have also attached some images that may be useful, but will need a new logo for BRELWIN Care. I have attached some logo idea's, it is up to you decide whether you want to use them.
I would prefer the homepage as full screen image, and the categories offered as a drop down or over the main image.
I have also attached linked to some competitors websites:
https://www.vorimant-health.co.uk/
http://www.qlbn.org.uk/
Industry/Entity Type
Clinic
Number of Pages Required
1 page
Font styles to use
Look and feel
Each slider illustrates characteristics of the customer's brand and the style your logo design should communicate.

```html
<!DOCTYPE html>
<html lang="en">
<head>
<meta charset="utf-8">
<title>BRELWIN Care – Child &amp; Adolescent Mental Health</title>
<link rel="stylesheet" href="https://fonts.googleapis.com/css2?family=Cabin+Condensed:wght@400;500;600;700&display=swap">
<style>
:root{
  --yellow:#ffec00;
  --purple:#6e1f80;
  --pink:#e6007e;
  --green:#9cc83a;
  --teal:#13b0c9;
  --navy:#27358a;
  --violet:#6b1fc2;
  --orange:#ff6400;
  --blue:#0b5cff;
  --grey:#dedede;
  --white:#ffffff;
  --ink:#222222;
  --font:"Cabin Condensed", "Arial Narrow", sans-serif;
}
*{box-sizing:border-box;margin:0;padding:0}
html,body{width:1200px;height:2655px;overflow:hidden;background:var(--white)}
body{font-family:var(--font);color:var(--white)}
.canvas{position:relative;width:1200px;height:2655px;overflow:hidden}

/* sidebar */
.sidebar{position:absolute;left:0;top:0;width:159px;height:2580px;background:var(--grey)}
.nav-item{position:absolute;left:0;width:159px;display:flex;flex-direction:column;align-items:center;justify-content:flex-end;padding-bottom:16px;font-size:15px;font-weight:600;text-transform:uppercase;letter-spacing:.3px}
.nav-item svg{margin-bottom:16px}
.nav-menu{top:0;height:147px;background:var(--yellow);color:var(--ink)}
.nav-about{top:147px;height:173px;background:var(--purple)}
.nav-team{top:320px;height:172px;background:var(--pink)}
.nav-services{top:492px;height:173px;background:var(--green)}
.nav-contact{top:665px;height:174px;background:var(--teal)}
.nav-parents{top:839px;height:170px;background:var(--navy)}
.nav-commissioners{top:1009px;height:173px;background:var(--violet)}
.nav-blog{top:1182px;height:174px;background:var(--orange)}
.nav-forum{top:1356px;height:173px;background:var(--blue)}

/* header */
.site-header{position:absolute;left:159px;top:0;width:1041px;height:147px;background:var(--white);display:flex;align-items:center;justify-content:center}
.brand{display:flex;align-items:center;gap:14px;font-size:40px;font-weight:700;color:var(--pink);letter-spacing:1px}
.brand-dot{width:40px;height:40px;border-radius:50%;background:var(--yellow)}

/* hero */
.hero-panel{position:absolute;top:147px;height:518px;display:flex;align-items:flex-end;padding-bottom:20px}
.hero-parents{left:159px;width:519px;background:linear-gradient(135deg,#6d78b8 0%,#4a5aa6 55%,#3c4a92 100%);padding-left:66px}
.hero-commissioners{left:678px;width:522px;background:linear-gradient(135deg,#f063b6 0%,#e0239a 55%,#c91c86 100%);padding-left:60px}
.hero-label{font-size:64px;font-weight:600;line-height:1;text-transform:uppercase}
.hero-pointer{position:absolute;left:662px;top:640px}

/* banner */
.slide-banner{position:absolute;left:159px;top:665px;width:1041px;height:174px;background:var(--orange);display:flex;align-items:center;justify-content:center;text-align:center}
.slide-banner h2{font-size:46px;font-weight:500;line-height:1.1}
.slide-arrow{position:absolute;top:62px}
.slide-prev{left:40px}
.slide-next{right:40px}

/* about */
.about{position:absolute;left:159px;top:839px;width:1041px;height:517px;background:linear-gradient(120deg,#8a4da0 0%,#7a3b95 50%,#6a2c86 100%);text-align:center}
.section-title{font-size:46px;font-weight:600;text-transform:uppercase;line-height:1}
.title-rule{width:97px;height:4px;background:var(--orange);margin:14px auto 0}
.about .section-title{padding-top:104px}
.about-text{width:660px;margin:44px auto 0;font-size:13.5px;line-height:27px}
.about-text p+p{margin-top:20px}
.btn-more{display:inline-block;margin-top:26px;width:157px;height:41px;line-height:41px;background:var(--green);color:var(--ink);font-size:14px;font-weight:600;text-transform:uppercase;letter-spacing:.5px}

/* blog */
.blog{position:absolute;left:159px;top:1356px;width:1041px;height:584px;background:linear-gradient(120deg,#a6cd3f 0%,#9cc43a 50%,#8fb62f 100%);text-align:center}
.blog .section-title{padding-top:62px;text-transform:uppercase}
.blog .title-rule{background:var(--orange);margin-top:12px}
.post{position:absolute;top:161px;width:285px}
.post-1{left:62px}.post-2{left:376px}.post-3{left:689px}
.post-image{position:relative;height:202px;border:3px solid var(--white)}
.post-image-1{background:linear-gradient(135deg,#e9c27a,#7d8f4b)}
.post-image-2{background:linear-gradient(135deg,#f1e7d6,#c9a07a)}
.post-image-3{background:linear-gradient(135deg,#e2e4e8,#b7a48f)}
.post-date{position:absolute;left:3px;top:3px;background:var(--pink);font-size:13px;padding:3px 10px}
.post-title{margin-top:24px;font-size:19px;font-weight:600;line-height:22px}
.post-excerpt{margin-top:10px;font-size:12px;line-height:16px;padding:0 14px}
.post-by{margin-top:14px;font-size:11px;font-weight:600}
.post-by span{color:var(--pink);font-size:15px}

/* contact */
.contact{position:absolute;left:159px;top:1940px;width:1041px;height:640px;background:linear-gradient(120deg,#23bcd0 0%,#17b1c9 50%,#0fa3bd 100%)}
.contact .section-title{position:absolute;left:0;width:100%;top:70px;text-align:center;text-transform:uppercase}
.contact .title-rule{position:absolute;left:472px;top:126px;margin:0}
.field{position:absolute;width:273px;border-bottom:2px solid var(--white);font-size:16px;font-weight:500}
.field-name{left:62px;top:234px;height:33px}
.field-email{left:62px;top:324px;height:26px}
.field-phone{left:62px;top:412px;height:29px}
.field-message{left:367px;top:234px;height:198px}
.btn-send{position:absolute;left:62px;top:473px;width:160px;height:42px;background:var(--yellow);color:var(--ink);font-size:15px;font-weight:600;text-align:center;line-height:42px;text-transform:uppercase}
.divider{position:absolute;left:662px;top:205px;width:2px;height:383px;background:rgba(255,255,255,.8)}
.info{position:absolute;left:698px;top:255px;list-style:none;font-size:16px;font-weight:500}
.info li{display:flex;align-items:flex-start;gap:20px;margin-bottom:14px;line-height:22px}
.info svg{flex:none;margin-top:3px}

/* footer */
.site-footer{position:absolute;left:0;top:2580px;width:1200px;height:75px;background:var(--white);color:var(--ink);text-align:center;line-height:75px;font-size:15px;font-weight:600}
</style>
</head>
<body>
<div class="canvas">

  <nav class="sidebar" aria-label="Main">
    <div class="nav-item nav-menu">
      <svg width="52" height="30" viewBox="0 0 52 30" fill="none" stroke="#222" stroke-width="2"><path d="M2 3h48M2 11h48M10 19h40M2 27h48"/></svg>Menu
    </div>
    <div class="nav-item nav-about">
      <svg width="64" height="60" viewBox="0 0 64 60" fill="none" stroke="#e6007e" stroke-width="4"><path d="M4 6h22l6 6v44l-6-5H4z"/><path d="M60 6H38l-6 6v44l6-5h22z" fill="#e6007e"/><path d="M42 20h12M42 28h12M42 36h12" stroke="#fff" stroke-width="2"/></svg>About
    </div>
    <div class="nav-item nav-team">
      <svg width="66" height="62" viewBox="0 0 66 62" fill="none" stroke="#fff" stroke-width="3"><circle cx="33" cy="10" r="7"/><path d="M22 30a11 9 0 0 1 22 0z"/><circle cx="16" cy="34" r="7"/><path d="M5 56a11 9 0 0 1 22 0z"/><circle cx="50" cy="34" r="7"/><path d="M39 56a11 9 0 0 1 22 0z"/></svg>Our Team
    </div>
    <div class="nav-item nav-services">
      <svg width="66" height="66" viewBox="0 0 66 66" fill="none" stroke="#fff" stroke-width="3" stroke-linejoin="round"><path d="M44 4a16 16 0 0 0-14 22L6 50a6 6 0 0 0 9 9l24-24a16 16 0 0 0 22-14l-9 9-9-3-3-9 9-9z"/></svg>Our Services
    </div>
    <div class="nav-item nav-contact">
      <svg width="64" height="62" viewBox="0 0 64 62" fill="none" stroke="#fff" stroke-width="4" stroke-linejoin="round"><path d="M4 30L32 4l28 26"/><path d="M11 24v34h42V24"/><path d="M26 58V40h12v18"/></svg>Contact Us
    </div>
    <div class="nav-item nav-parents">
      <svg width="62" height="62" viewBox="0 0 62 62" fill="#fff"><circle cx="16" cy="9" r="7"/><circle cx="46" cy="9" r="7"/><path d="M2 22h24l5 14 5-14h24v38H46V36l-9 12h-12l-9-12v24H2z"/></svg>Parents
    </div>
    <div class="nav-item nav-commissioners">
      <svg width="60" height="66" viewBox="0 0 60 66" fill="none" stroke="#fff" stroke-width="3" stroke-linejoin="round"><circle cx="30" cy="24" r="20"/><path d="M20 24l7 7 13-13"/><path d="M18 40v22l12-8 12 8V40"/></svg>Commisioners
    </div>
    <div class="nav-item nav-blog">
      <svg width="72" height="52" viewBox="0 0 72 52" fill="none" stroke="#fff" stroke-width="3" stroke-linejoin="round"><path d="M4 18h12l40-14v40L16 30H4z"/><path d="M14 30l4 18h8l-3-16"/><path d="M62 16v16"/></svg>Blog
    </div>
    <div class="nav-item nav-forum">
      <svg width="62" height="58" viewBox="0 0 62 58" fill="none" stroke="#fff" stroke-width="3" stroke-linejoin="round"><path d="M14 20V4h34v16"/><path d="M4 20h54v22H4z"/><path d="M14 34v20h34V34z" fill="var(--blue)"/><path d="M22 42h18M22 48h18"/></svg>Forum
    </div>
  </nav>

  <header class="site-header">
    <div class="brand"><span class="brand-dot"></span>BRELWIN</div>
  </header>

  <section class="hero-panel hero-parents" role="img" aria-label="Photo of a parent talking with a child, tinted blue">
    <span class="hero-label">Parents</span>
  </section>
  <section class="hero-panel hero-commissioners" role="img" aria-label="Photo of a clinician in a meeting, tinted pink">
    <span class="hero-label">Commisioners</span>
  </section>
  <svg class="hero-pointer" width="32" height="26" viewBox="0 0 32 26"><path d="M0 26L16 0l16 26z" fill="var(--orange)"/></svg>

  <section class="slide-banner">
    <svg class="slide-arrow slide-prev" width="48" height="48" viewBox="0 0 48 48" fill="none" stroke="#fff" stroke-width="3" stroke-linejoin="round"><path d="M44 6L4 24l40 18-14-18z"/></svg>
    <h2>ADHD and autism screening<br>within 24 hours</h2>
    <svg class="slide-arrow slide-next" width="48" height="48" viewBox="0 0 48 48" fill="none" stroke="var(--green)" stroke-width="3" stroke-linejoin="round"><path d="M4 6l40 18L4 42l14-18z"/></svg>
  </section>

  <section class="about" role="img" aria-label="Photo of a child at a table, tinted purple">
    <h2 class="section-title">About Us</h2>
    <div class="title-rule"></div>
    <div class="about-text">
      <p>BRELWIN Care was formed with a vision to provide the very best BRELWIN assessments, therapy and aftercare. We have unique modern pathways that allow children and adolescents to be seen quickly by handpicked clinicians that are highly skilled and some of the best in their chosen field.</p>
      <p>We have a turnaround time of 24 hours for all ADHD and ASD screening, and aim to have see any child for a full ASD, or ADHD assessment within 14 days. If your child has been diagnosed with ADHD or ASD we offer the very best post diagnosis support to both the child and family.</p>
    </div>
    <span class="btn-more">Read More</span>
  </section>

  <section class="blog" role="img" aria-label="Photo of a mother and child, tinted green">
    <h2 class="section-title">Blog</h2>
    <div class="title-rule"></div>
    <article class="post post-1">
      <div class="post-image post-image-1" role="img" aria-label="Photo of a child holding a parent's hand outdoors"><span class="post-date">Jan 20th 2017</span></div>
      <h3 class="post-title">At vero eos et accusamus et iusto odio dignissimos</h3>
      <p class="post-excerpt">Dolores et quas molestias excepturi sint occaecati cupiditate non provident, similique sunt in culpa qui officia deserunt mollitia animi</p>
      <p class="post-by">Posted By <span>BRELWIN</span></p>
    </article>
    <article class="post post-2">
      <div class="post-image post-image-2" role="img" aria-label="Photo of a child working at a desk with a teacher"><span class="post-date">Jan 20th 2017</span></div>
      <h3 class="post-title">At vero eos et accusamus et iusto odio dignissimos</h3>
      <p class="post-excerpt">Dolores et quas molestias excepturi sint occaecati cupiditate non provident, similique sunt in culpa qui officia deserunt mollitia animi</p>
      <p class="post-by">Posted By <span>BRELWIN</span></p>
    </article>
    <article class="post post-3">
      <div class="post-image post-image-3" role="img" aria-label="Photo of two young children in a classroom"><span class="post-date">Jan 20th 2017</span></div>
      <h3 class="post-title">At vero eos et accusamus et iusto odio dignissimos</h3>
      <p class="post-excerpt">Dolores et quas molestias excepturi sint occaecati cupiditate non provident, similique sunt in culpa qui officia deserunt mollitia animi</p>
      <p class="post-by">Posted By <span>BRELWIN</span></p>
    </article>
  </section>

  <section class="contact" role="img" aria-label="Photo of a group of smiling teenagers on a sofa, tinted teal">
    <h2 class="section-title">Contact Us</h2>
    <div class="title-rule"></div>
    <div class="field field-name">Name</div>
    <div class="field field-email">E-Mail</div>
    <div class="field field-phone">Phone</div>
    <div class="field field-message">Message</div>
    <span class="btn-send">Send</span>
    <div class="divider"></div>
    <ul class="info">
      <li><svg width="14" height="18" viewBox="0 0 14 18" fill="var(--yellow)"><path d="M7 0a7 7 0 0 0-7 7c0 5 7 11 7 11s7-6 7-11a7 7 0 0 0-7-7zm0 10a3 3 0 1 1 0-6 3 3 0 0 1 0 6z"/></svg><span>Harwick Suite 2B, 41-47 Marlow Road,<br>London, E99 4ZZ</span></li>
      <li><svg width="16" height="16" viewBox="0 0 16 16" fill="var(--yellow)"><path d="M3 0l3 4-2 2a10 10 0 0 0 6 6l2-2 4 3-2 3C7 16 0 9 0 3z"/></svg><span>0203 555 0182</span></li>
      <li><svg width="16" height="16" viewBox="0 0 16 16" fill="none" stroke="var(--yellow)" stroke-width="2"><circle cx="8" cy="8" r="7"/><path d="M8 4v4l3 2"/></svg><span>9am – 5pm Mon-Fri</span></li>
      <li><svg width="18" height="14" viewBox="0 0 18 14" fill="none" stroke="var(--yellow)" stroke-width="2"><rect x="1" y="1" width="16" height="12"/><path d="M1 1l8 7 8-7"/></svg><span>enquiry@brelwincare.co.uk</span></li>
    </ul>
  </section>

  <footer class="site-footer">© 2018 Compnay Name | &nbsp;All Rights Reserved</footer>
</div>
</body>
</html>
```